Book for new dads needs a cover.

We need a cover for a book titled Roadmap to Early Parenthood: Practical Methods for Welcoming a Newborn, Juggling Career and Home Life, and Managing Mental Health on the Path to Becoming a Parent. We would like to see a design that emphasizes healthy babies and confident dads.

```html
<!DOCTYPE html>
<html lang="en">
<head>
<meta charset="utf-8">
<title>Roadmap to Early Parenthood – Book Cover</title>
<link rel="stylesheet" href="https://fonts.googleapis.com/css2?family=Bebas+Neue&family=Oswald:wght@500&display=swap">
<style>
  :root {
    --page: #ffffff;
    --orange: #e67a3c;
    --orange-light: #eb8a4a;
    --navy: #1b2e66;
    --white: #ffffff;
    --skin: #8a5a3e;
    --shirt: #f1efec;
  }
  html, body {
    margin: 0;
    width: 1200px;
    height: 1000px;
    overflow: hidden;
    background: var(--page);
  }
  .canvas {
    position: relative;
    width: 1200px;
    height: 1000px;
  }
  .cover {
    position: absolute;
    left: 268px;
    top: 0;
    width: 664px;
    height: 1000px;
    background: linear-gradient(180deg, var(--orange-light) 0%, var(--orange) 60%);
    overflow: hidden;
  }
  .title-line {
    position: absolute;
    margin: 0;
    color: var(--white);
    font-family: "Bebas Neue", "Oswald", sans-serif;
    font-weight: 400;
    line-height: 1;
    white-space: nowrap;
    z-index: 3;
  }
  .title-main { left: 20px; top: 18px; font-size: 196px; letter-spacing: 2px; }
  .title-to { left: 44px; top: 196px; font-size: 66px; }
  .title-rule {
    position: absolute;
    left: 104px;
    top: 214px;
    width: 292px;
    height: 5px;
    background: var(--white);
  }
  .title-early { left: 44px; top: 250px; font-size: 104px; }
  .title-band {
    position: absolute;
    left: 0;
    top: 347px;
    width: 489px;
    height: 213px;
    background: var(--navy);
  }
  .title-parent { left: 24px; top: 405px; font-size: 106px; letter-spacing: 1px; }

  .subtitle {
    position: absolute;
    left: 42px;
    top: 582px;
    width: 272px;
    z-index: 3;
  }
  .subtitle-lead {
    margin: 0 0 8px;
    color: var(--navy);
    font-family: "Bebas Neue", "Oswald", sans-serif;
    font-size: 32px;
    line-height: 1.0;
  }
  .subtitle-rest {
    margin: 0;
    color: var(--white);
    font-family: "Oswald", sans-serif;
    font-weight: 500;
    font-size: 16px;
    line-height: 1.55;
    text-transform: uppercase;
  }

  .art {
    position: absolute;
  }
  .art-diaper { left: 470px; top: 195px; width: 142px; height: 125px; background: #b9a6e0; border-radius: 18px 18px 50px 50px; transform: rotate(14deg); }
  .art-pin { left: 40px; top: 790px; width: 72px; height: 84px; background: #f2b428; border-radius: 30px; opacity: .85; }
  .art-bear { left: 134px; top: 792px; width: 78px; height: 104px; background: #f5b3d0; border-radius: 40px; }
  .art-bottle { left: 232px; top: 780px; width: 60px; height: 126px; background: linear-gradient(180deg, #f1b43a 0 18%, #8fd3e0 18% 28%, #f7dde6 28%); border-radius: 14px 14px 10px 10px; }

  .photo {
    position: absolute;
    left: 340px;
    top: 400px;
    width: 324px;
    height: 600px;
    background: linear-gradient(160deg, var(--skin) 0%, #a5715a 30%, var(--shirt) 55%, #e3e0dc 100%);
    clip-path: polygon(165px 0, 100% 0, 100% 100%, 0 100%, 0 160px, 165px 160px);
    z-index: 2;
  }

  .author-band {
    position: absolute;
    left: 0;
    bottom: 0;
    width: 664px;
    height: 68px;
    background: var(--navy);
    z-index: 1;
  }
  .author {
    position: absolute;
    left: 36px;
    top: 14px;
    margin: 0;
    color: var(--white);
    font-family: "Oswald", sans-serif;
    font-weight: 500;
    font-size: 28px;
    letter-spacing: 4px;
    line-height: 40px;
    text-transform: uppercase;
    white-space: nowrap;
  }
</style>
</head>
<body>
<div class="canvas">
  <div class="cover">
    <h1 class="title-line title-main">Roadmap</h1>
    <p class="title-line title-to">To</p>
    <div class="title-rule"></div>
    <p class="title-line title-early">Early</p>
    <div class="title-band"></div>
    <p class="title-line title-parent">Parenthood</p>

    <div class="art art-diaper" role="img" aria-label="Illustration of a lavender cloth diaper with a safety pin"></div>

    <div class="subtitle">
      <p class="subtitle-lead">Practical Methods for Welcoming a Newborn,</p>
      <p class="subtitle-rest">Juggling career and home life, and managing mental health on the path to becoming a parent</p>
    </div>

    <div class="art art-pin" role="img" aria-label="Illustration of yellow safety pins"></div>
    <div class="art art-bear" role="img" aria-label="Illustration of a pink teddy bear"></div>
    <div class="art art-bottle" role="img" aria-label="Illustration of a baby bottle"></div>

    <div class="photo" role="img" aria-label="Photograph of a smiling father in a white t-shirt holding his baby"></div>

    <div class="author-band">
      <p class="author">Dana R. Whitfield</p>
    </div>
  </div>
</div>
</body>
</html>
```